Corvana Tongue Works, LLC

We need a business card that includes information about our business and conveys a reliable business that provides document translation services and interpreters for a variety of corporate and individual clients. We want to come across as professional, reliable, yet approachable. It should include the following on one side:

ESL / ENL Language Classes, Private Lessons, and Online Tutors
PLEXA Training and Testing
Translating & Interpreting Services
Contact us about Over-the-Phone Interpreting in over 200 languages
24/7/365
www.corvanatongue.example

The other side should include (555) 481-3062

Rhoda Pelling, President
482 Garnet Ave., Ste. 219
Indianapolis, IN 40917

Please add USA as part of the address. Also, please add rmpelling@corvanatongueworks.example as the e-mail address. Thank you.

Target Market(s)

Business professionals, their families, the international community

Industry/Entity Type

Business

Contact Information for Business Card

24/7/365
www.corvanatongue.example

(555) 481-3062

Rhoda Pelling, President
482 Garnet Ave., Ste. 219
Indianapolis, IN 40917
USA

Font styles to use
Sans Serif

Colors

Designer to choose colors to be used in the design.

Requirements
Must have
• See project description
• e-mail address and web address
• Phone number
Nice to have
• a globe
• physical address
Should not have
• Should not have the same color scheme as other agencies in our market in Indiana unless it is blue and black. No purple or yellow.

```html
<!DOCTYPE html>
<html lang="en">
<head>
<meta charset="utf-8">
<title>Corvana Tongue Works – Business Card</title>
<link href="https://fonts.googleapis.com/css2?family=Lato:wght@400;700&display=swap" rel="stylesheet">
<style>
  :root {
    --stage: #3a3532;
    --card: #0d0d0e;
    --blue: #1f91d8;
    --white: #ffffff;
    --silver: #d4d7da;
    --rule: #4a4a4c;
  }
  * { margin: 0; padding: 0; box-sizing: border-box; }
  html, body { width: 1200px; height: 900px; overflow: hidden; }
  body {
    background: var(--stage);
    font-family: "Lato", "Helvetica Neue", Arial, sans-serif;
    position: relative;
  }
  .card {
    position: absolute;
    width: 540px;
    height: 309px;
    background: var(--card);
    overflow: hidden;
    box-shadow: 0 10px 30px rgba(0,0,0,.45);
  }
  .card--front { left: 30px; top: 296px; }
  .card--back  { left: 630px; top: 296px; }

  /* Front */
  .brand {
    position: absolute;
    left: 28px; top: 104px;
    display: flex; align-items: center; gap: 12px;
  }
  .brand__dot {
    width: 78px; height: 78px; border-radius: 50%;
    background: var(--blue); flex: none;
  }
  .brand__name {
    color: var(--white);
    font-weight: 400;
    font-size: 24px;
    line-height: 25px;
  }
  .brand__name small { font-size: 11px; }
  .divider {
    position: absolute; left: 246px; top: 56px;
    width: 1px; height: 196px; background: var(--rule);
  }
  .contact {
    position: absolute; left: 266px; top: 62px;
    color: var(--white);
  }
  .contact__name {
    color: var(--blue); font-weight: 700; font-size: 18px;
    letter-spacing: .5px; text-transform: uppercase;
  }
  .contact__title { font-size: 13px; margin-bottom: 8px; }
  .contact__line {
    display: flex; align-items: center; gap: 6px;
    font-size: 14px; line-height: 21px;
    white-space: nowrap;
  }
  .contact__line svg { width: 11px; height: 11px; flex: none; }
  .contact__address { margin-top: 12px; font-size: 14px; line-height: 20px; }

  /* Back */
  .back-brand {
    position: absolute; left: 0; right: 0; top: 28px;
    display: flex; justify-content: center; align-items: center; gap: 10px;
  }
  .back-brand__dot {
    width: 58px; height: 58px; border-radius: 50%;
    background: var(--silver); flex: none;
  }
  .back-brand__name {
    color: var(--silver); font-size: 18px; line-height: 19px;
  }
  .back-brand__name small { font-size: 9px; }
  .services {
    position: absolute; left: 30px; top: 118px;
    list-style: none; color: var(--silver);
    font-size: 13px; line-height: 19px;
  }
  .services li { display: flex; align-items: center; gap: 8px; }
  .services li::before {
    content: ""; width: 6px; height: 6px; border-radius: 50%;
    background: var(--blue); flex: none;
  }
  .band {
    position: absolute; left: 0; right: 0; bottom: 0; height: 84px;
    background: var(--blue); color: var(--white);
    display: flex; flex-direction: column; justify-content: center; align-items: flex-end;
    padding-right: 70px; font-size: 15px; line-height: 22px;
  }
  .band__inner { text-align: center; }
</style>
</head>
<body>

  <section class="card card--front" aria-label="Business card front">
    <div class="brand">
      <span class="brand__dot"></span>
      <p class="brand__name">Corvana<br>Tongue<br>Works <small>LLC</small></p>
    </div>
    <span class="divider"></span>
    <div class="contact">
      <p class="contact__name">Rhoda Pelling</p>
      <p class="contact__title">President</p>
      <p class="contact__line">
        <svg viewBox="0 0 24 24" aria-hidden="true"><path fill="#1f91d8" d="M6.6 10.8a15.1 15.1 0 0 0 6.6 6.6l2.2-2.2a1 1 0 0 1 1-.25 11.4 11.4 0 0 0 3.6.57 1 1 0 0 1 1 1V20a1 1 0 0 1-1 1A17 17 0 0 1 3 4a1 1 0 0 1 1-1h3.5a1 1 0 0 1 1 1c0 1.25.2 2.45.57 3.6a1 1 0 0 1-.25 1z"/></svg>
        (555) 481-3062
      </p>
      <p class="contact__line">
        <svg viewBox="0 0 24 24" aria-hidden="true"><rect x="2" y="5" width="20" height="14" rx="2" fill="#1f91d8"/><path d="M3 6l9 7 9-7" stroke="#0d0d0e" stroke-width="1.8" fill="none"/></svg>
        rmpelling@corvanatongueworks.example
      </p>
      <p class="contact__line">
        <svg viewBox="0 0 24 24" aria-hidden="true"><circle cx="12" cy="12" r="10" fill="#1f91d8"/><path d="M2 12h20M12 2a15 15 0 0 1 0 20M12 2a15 15 0 0 0 0 20" stroke="#0d0d0e" stroke-width="1.6" fill="none"/></svg>
        www.corvanatongue.example
      </p>
      <p class="contact__address">482 Garnet Ave., Ste. 219<br>Indianapolis, IN 40917 USA</p>
    </div>
  </section>

  <section class="card card--back" aria-label="Business card back">
    <div class="back-brand">
      <span class="back-brand__dot"></span>
      <p class="back-brand__name">Corvana<br>Tongue<br>Works <small>LLC</small></p>
    </div>
    <ul class="services">
      <li>ESL / ENL Language Classes, Private Lessons, and Online Tutors</li>
      <li>PLEXA Training and Testing</li>
      <li>Translating &amp; Interpreting Services</li>
      <li>Contact us about Over-the-Phone Interpreting in over 200 languages</li>
    </ul>
    <div class="band">
      <div class="band__inner">
        <p>24/7/365</p>
        <p>www.corvanatongue.example</p>
      </div>
    </div>
  </section>

</body>
</html>
```